A start up special flyer design!

Hi All - Have updated the attachment content - This is the info required for the designs.
I need a catchy flyer to send out to a few areas to advertise the start of my plumbing business!
The flyer will contain an offer for customers, which will need to have some key details on it. See attached. Feel free to fit these criteria into the flyer given your knowledge on design and messaging principles. Key thing to get across to customers is the discount and special offer, and that it is a start up offer.
I have a logo that needs to be on the flyer as well - let me know what format you require and I will send through to you.
The color scheme needs to be blue / grey / black / white.
Let me know if you have any questions.
I

```html
<!DOCTYPE html>
<html lang="en">
<head>
<meta charset="utf-8">
<title>Plumbing Start-Up Offer Flyer</title>
<link rel="stylesheet" href="https://fonts.googleapis.com/css2?family=Arimo:ital,wght@0,400;0,700;1,400;1,700&family=Roboto+Condensed:wght@700&family=Montserrat:wght@700&display=swap">
<style>
:root{
  --blue:#1e8be2;
  --blue-light:#5db3f0;
  --blue-pale:#bfe0f8;
  --grey-logo:#a5a5a5;
  --grey-bg:#ececec;
  --ink:#111111;
  --white:#ffffff;
  --tick-dark:#4fae2b;
  --tick-light:#8fd65a;
  --photo-main-a:#8a8f96;
  --photo-main-b:#cfd3d8;
  --photo-inset-a:#3c5a7a;
  --photo-inset-b:#b0563f;
}
*{margin:0;padding:0;box-sizing:border-box}
html,body{width:849px;height:1200px;overflow:hidden}
body{background:var(--white);font-family:"Arimo",Arial,sans-serif;color:var(--ink)}
.flyer{position:relative;width:849px;height:1200px;overflow:hidden;
  background:linear-gradient(180deg,var(--grey-bg) 0%,#f7f7f7 40%,#f4f4f4 100%)}
.shapes{position:absolute;inset:0}
.logo{position:absolute;left:37px;top:67px;width:275px;height:117px;background:var(--grey-logo);
  display:flex;align-items:center;justify-content:center;
  font-family:"Montserrat",sans-serif;font-weight:700;font-size:96px;color:var(--white);letter-spacing:2px}
.services{position:absolute;left:370px;top:88px;list-style:none}
.services li{display:flex;align-items:center;height:26.5px;font-weight:700;font-size:18.5px}
.tick{flex:none}
.services .tick{width:20px;height:16px;margin-right:10px}
.offers{position:absolute;left:55px;top:795px;list-style:none;color:var(--white);
  font-family:"Roboto Condensed",sans-serif;font-weight:700;font-size:30px;line-height:38px}
.offers li{display:flex;align-items:flex-start;margin-bottom:15px}
.offers .tick{width:38px;height:32px;margin-right:16px;margin-top:3px}
.booking{position:absolute;left:0;width:849px;top:1022px;text-align:center;font-style:italic;font-size:19px;line-height:30px}
.booking strong{font-weight:700}
.footnotes{position:absolute;left:57px;top:1130px;font-size:11.5px;line-height:14px}
.contact{position:absolute;left:508px;top:1102px;list-style:none}
.contact li{display:flex;align-items:center;height:27px;font-size:15px}
.contact li.phone{font-weight:700;font-size:18.5px}
.contact svg{width:16px;height:16px;margin-right:14px;flex:none}
</style>
</head>
<body>
<div class="flyer">
  <svg class="shapes" width="849" height="1200" viewBox="0 0 849 1200">
    <defs>
      <linearGradient id="mainPhoto" x1="0" y1="0" x2="1" y2="1">
        <stop offset="0" stop-color="var(--photo-main-b)"/>
        <stop offset="0.5" stop-color="var(--photo-main-a)"/>
        <stop offset="1" stop-color="var(--photo-main-b)"/>
      </linearGradient>
      <linearGradient id="insetPhoto" x1="0" y1="0" x2="1" y2="1">
        <stop offset="0" stop-color="var(--photo-inset-a)"/>
        <stop offset="0.6" stop-color="var(--photo-inset-b)"/>
        <stop offset="1" stop-color="var(--photo-inset-a)"/>
      </linearGradient>
    </defs>
    <path class="band-top" d="M0,282 Q420,200 849,240 L849,700 L0,700 Z" fill="var(--blue)"/>
    <path role="img" aria-label="Photo of a smiling plumber with arms crossed, standing beside a silver work van" d="M0,300 Q420,232 849,262 L849,650 Q430,760 0,742 Z" fill="url(#mainPhoto)"/>
    <path class="inset-frame" d="M262,282 Q560,232 849,246 L849,450 Q700,470 570,440 Q420,400 345,330 Q300,295 262,282 Z" fill="var(--blue-light)"/>
    <path role="img" aria-label="Close-up photo of a plumber's hands holding a pipe wrench and hoses beside a tool belt" d="M280,285 Q560,240 849,252 L849,440 Q700,458 575,430 Q430,392 355,325 Q315,295 280,285 Z" fill="url(#insetPhoto)"/>
    <path class="band-accent" d="M0,760 Q430,700 849,605 L849,640 Q430,730 0,770 Z" fill="var(--blue-pale)"/>
    <path class="band-offer" d="M0,748 Q430,725 849,620 L849,900 Q480,1010 0,1003 Z" fill="var(--blue)"/>
  </svg>

  <div class="logo">LOGO</div>

  <ul class="services">
    <li><svg class="tick" viewBox="0 0 20 16"><path d="M2,8 L8,14 L18,2" fill="none" stroke="var(--tick-dark)" stroke-width="3"/></svg>All plumbing, draining, and gasfitting works</li>
    <li><svg class="tick" viewBox="0 0 20 16"><path d="M2,8 L8,14 L18,2" fill="none" stroke="var(--tick-dark)" stroke-width="3"/></svg>“Quality work at a decent price”</li>
    <li><svg class="tick" viewBox="0 0 20 16"><path d="M2,8 L8,14 L18,2" fill="none" stroke="var(--tick-dark)" stroke-width="3"/></svg>“Local plumber”</li>
  </ul>

  <ul class="offers">
    <li><svg class="tick" viewBox="0 0 38 32"><path d="M3,16 L14,28 L35,3" fill="none" stroke="var(--tick-light)" stroke-width="5"/></svg>15% off your overall bill*</li>
    <li><svg class="tick" viewBox="0 0 38 32"><path d="M3,16 L14,28 L35,3" fill="none" stroke="var(--tick-light)" stroke-width="5"/></svg>No GST payable, saving you additional 10% on your bill^</li>
    <li><svg class="tick" viewBox="0 0 38 32"><path d="M3,16 L14,28 L35,3" fill="none" stroke="var(--tick-light)" stroke-width="5"/></svg><span>Plus, a free hot water health check and<br>replacement quote~</span></li>
  </ul>

  <p class="booking">To make an appointment, <strong>call or email Declan,</strong><br>or alternatively make a <strong>booking directly on the website</strong></p>

  <p class="footnotes">*Offer valid between 15 August 2016 to 15 October 2016<br>^Valid until 30 September 2016.<br>~Quote valid for 12 months from the quote date.</p>

  <ul class="contact">
    <li class="phone"><svg viewBox="0 0 16 16"><path d="M3,1 L6,1 L7,5 L5,6.5 Q6.5,9.5 9.5,11 L11,9 L15,10 L15,13 Q14,15 11,15 Q1,12 1,3 Q1,1 3,1 Z" fill="var(--blue)"/></svg>0400 123 456</li>
    <li><svg viewBox="0 0 16 16"><rect x="1" y="3" width="14" height="10" fill="var(--blue)"/><path d="M1,3 L8,9 L15,3" fill="none" stroke="var(--white)" stroke-width="1.3"/></svg>declan@declanplumbing.com</li>
    <li><svg viewBox="0 0 16 16"><g fill="none" stroke="var(--blue)" stroke-width="1.4"><circle cx="8" cy="8" r="6.5"/><ellipse cx="8" cy="8" rx="3" ry="6.5"/><path d="M1.5,8 H14.5 M2.5,4.5 H13.5 M2.5,11.5 H13.5"/></g></svg>www.declanplumbing.com</li>
  </ul>
</div>
</body>
</html>
```